Business Card for Lantern Reach

Please design a Modern Business card for a Online Marketing Company

Website: http://www.lanternreach-example.com.au

Please do NOT include physical address in design.

```html
<!DOCTYPE html>
<html lang="en">
<head>
<meta charset="utf-8">
<title>Lantern Reach – Business Card</title>
<link rel="stylesheet" href="https://fonts.googleapis.com/css2?family=Open+Sans:wght@400;600&display=swap">
<style>
  :root {
    --brand-red: #c20b1d;
    --brand-orange: #f5820f;
    --ink-navy: #1c2a4a;
    --ink-grey: #4a4a4a;
    --ink-dark: #333333;
    --card-white: #ffffff;
    --stage: #e9e6e2;
  }
  * { margin: 0; padding: 0; box-sizing: border-box; }
  html, body { width: 1200px; height: 483px; overflow: hidden; background: var(--stage); }
  .stage {
    position: relative; width: 1200px; height: 483px;
    display: flex; align-items: center; justify-content: center; gap: 50px;
  }
  .card {
    position: relative; width: 540px; height: 310px; overflow: hidden;
    box-shadow: 0 6px 18px rgba(0,0,0,.18);
  }

  /* Front */
  .card--front { background: var(--card-white); }
  .front-brand { position: absolute; top: 74px; left: 0; right: 0; text-align: center; }
  .front-brand__name {
    font-family: "Open Sans", sans-serif; font-weight: 600;
    font-size: 32px; color: var(--brand-red); line-height: 1.1;
  }
  .front-brand__tagline {
    font-family: "Open Sans", sans-serif; font-weight: 600;
    font-size: 14px; color: var(--ink-dark); margin-top: 4px;
  }
  .holder {
    position: absolute; left: 118px; top: 186px; text-align: right;
    padding-right: 14px; border-right: 1px solid #cfcfcf; height: 64px;
    display: flex; flex-direction: column; justify-content: center;
  }
  .holder__name { font-family: "Open Sans", sans-serif; font-weight: 600; font-size: 20px; color: var(--ink-navy); line-height: 1.1; }
  .holder__title { font-family: "Open Sans", sans-serif; font-size: 17px; color: var(--ink-grey); }
  .contacts { position: absolute; left: 262px; top: 186px; list-style: none; }
  .contacts__item {
    display: flex; align-items: center; gap: 8px; height: 21px;
    font-family: "Open Sans", sans-serif; font-size: 13.5px; color: var(--ink-dark);
  }
  .contacts__icon { width: 13px; height: 13px; flex: none; }
  .front-bands { position: absolute; left: 0; bottom: 0; width: 540px; height: 80px; }

  /* Back */
  .card--back { background: var(--brand-red); color: #fff; }
  .back-brand { position: absolute; left: 0; right: 0; top: 90px; text-align: center; }
  .back-brand__name { font-family: "Open Sans", sans-serif; font-weight: 600; font-size: 44px; line-height: 1.1; }
  .back-brand__tagline { font-family: "Open Sans", sans-serif; font-weight: 600; font-size: 20px; margin-top: 4px; }
  .back-web {
    position: absolute; left: 0; right: 0; top: 224px; text-align: center;
    font-family: "Open Sans", sans-serif; font-size: 19px; letter-spacing: 1px;
  }
</style>
</head>
<body>
<main class="stage">
  <section class="card card--front" aria-label="Card front">
    <div class="front-brand">
      <div class="front-brand__name">Lantern Reach</div>
      <div class="front-brand__tagline">Be seen online - Grow online</div>
    </div>

    <div class="holder">
      <div class="holder__name">Your Name</div>
      <div class="holder__title">Title</div>
    </div>

    <ul class="contacts">
      <li class="contacts__item">
        <svg class="contacts__icon" viewBox="0 0 16 16"><circle cx="8" cy="8" r="8" fill="var(--brand-red)"/><path d="M5 4.5c.8-.6 1.3 0 1.6.8l-.8 1c.4 1 1 1.8 2 2.3l1-.8c.8.3 1.4.8.8 1.6-1.5 1.5-5.5-2.5-4.6-4.9z" fill="#fff"/></svg>
        0400 555 172
      </li>
      <li class="contacts__item">
        <svg class="contacts__icon" viewBox="0 0 16 16"><rect x="1" y="3" width="14" height="10" rx="1.5" fill="var(--brand-red)"/><path d="M2 4.5l6 4.5 6-4.5" fill="none" stroke="#fff" stroke-width="1.3"/></svg>
        plan@lanternreach-example.com.au
      </li>
      <li class="contacts__item">
        <svg class="contacts__icon" viewBox="0 0 16 16"><circle cx="8" cy="8" r="8" fill="var(--brand-red)"/><g fill="none" stroke="#fff" stroke-width="1"><circle cx="8" cy="8" r="5"/><ellipse cx="8" cy="8" rx="2.2" ry="5"/><path d="M3 8h10"/></g></svg>
        www.lanternreach-example.com.au
      </li>
    </ul>

    <svg class="front-bands" viewBox="0 0 540 80" preserveAspectRatio="none" aria-hidden="true">
      <polygon points="0,62 240,62 255,54 540,34 540,80 0,80" fill="var(--brand-red)"/>
      <polygon points="0,66 238,66 254,58 262,58 240,80 0,80" fill="var(--card-white)"/>
      <polygon points="0,68 236,68 222,80 0,80" fill="var(--brand-orange)"/>
    </svg>
  </section>

  <section class="card card--back" aria-label="Card back">
    <div class="back-brand">
      <div class="back-brand__name">Lantern Reach</div>
      <div class="back-brand__tagline">Be seen online - Grow online</div>
    </div>
    <div class="back-web">www.lanternreach-example.com.au</div>
  </section>
</main>
</body>
</html>
```